New website for out outstanding veterinary training center

We already have a beautiful logo with nice colors and we are now looking for a breathtaking modern website to present our training center and future corses held there. A section to book open courses should also be available.

We are planing the realize the website with Wordpress.
The following pages should be available:
- Startpage / Overview
- Page to present the different rooms and seating option
- Page where the rooms can be booked
- Page where recommended accommodation are presented
- Page to present and book corses
- contact page
- Impressum

Target Market(s)

European Union

Industry/Entity Type

Education, Veterinary medicine

Number of Pages Required

5+ page

Font styles to use
Sans Serif

Colors
00AB8E
00BBA5
67D7C9
C6EFE9
E9F9F6

Requirements
Must have
• The website must be clear and easy to read. The colors form the logos should be used for the design.
Should not have
• To playful design. The page is not for a veterinary practice. we are a training center for veterinarians!

```html
<!DOCTYPE html>
<html lang="en">
<head>
<meta charset="utf-8">
<title>Veterra Training Center – Homepage Layouts</title>
<link href="https://fonts.googleapis.com/css2?family=Poppins:ital,wght@0,400;0,500;0,600;1,400&display=swap" rel="stylesheet">
<style>
:root{
  --teal:#168a80;
  --teal-soft:#3ea59b;
  --ink:#4b3c47;
  --muted:#8a8088;
  --plum:#5c4956;
  --panel:#f6f6f6;
  --paper:#ffffff;
  --backdrop:#f2f2f2;
  --line:#dddddd;
  --map:#d6d2d6;
  --photo-hero:#8f8a6e;
  --photo-pets:#8a5e40;
  --photo-room:#c9c9cb;
  --photo-husky:#a99d92;
}
*{box-sizing:border-box;margin:0;padding:0}
html,body{width:691px;height:1200px;overflow:hidden;background:var(--backdrop);font-family:'Poppins',sans-serif;color:var(--ink)}
.stage{position:relative;width:1456px;height:2532px;transform:scale(.4746);transform-origin:0 0}
.page{position:absolute;top:75px;background:var(--paper);box-shadow:0 2px 10px rgba(0,0,0,.06);display:flex;flex-direction:column;overflow:hidden}
.page--a{left:167px;width:473px}
.page--b{left:806px;width:483px}
.section{position:relative;flex:none}
.section-title{font-size:14.5px;font-weight:500;text-align:center;color:var(--ink)}
.pill{display:inline-block;border-radius:20px;font-size:6.5px;font-weight:600;text-transform:uppercase;letter-spacing:.2px;padding:6px 10px;white-space:nowrap}
.pill--teal{background:var(--teal);color:#fff}
.pill--white{background:#fff;color:var(--ink)}

/* header */
.site-header{display:flex;justify-content:space-between;align-items:flex-start;padding:0 44px}
.brand{display:flex;align-items:center;gap:6px;margin-top:16px;font-size:14px;font-weight:600;color:var(--teal)}
.brand-dot{width:14px;height:14px;border-radius:50%;background:var(--teal)}
.header-right{text-align:right;padding-top:11px}
.header-contact{font-size:6.5px;color:var(--ink);display:flex;gap:4px;justify-content:flex-end;align-items:center;white-space:nowrap}
.header-contact svg{width:6px;height:6px;fill:var(--teal)}
.nav{display:flex;gap:9px;justify-content:flex-end;margin-top:12px;font-size:6px;font-weight:500;text-transform:uppercase}
.nav .is-active{color:var(--teal)}

/* hero */
.hero-media{position:absolute;inset:0;background:linear-gradient(90deg,#5a6a58 0%,var(--photo-hero) 45%,#3f9a8e 100%)}
.hero-copy{position:absolute;left:44px;top:58px}
.hero-title{font-size:20.5px;font-weight:600;color:#fff;text-transform:uppercase;line-height:1.27;letter-spacing:.2px}
.hero-copy .pill{margin-top:14px;padding:7px 10px}
.dots{position:absolute;left:50%;transform:translateX(-50%);display:flex;gap:2px}
.dots span{width:5px;height:5px;border-radius:50%;border:1px solid #fff}
.dots span:first-child{background:#fff}

/* welcome */
.welcome-copy{position:absolute;left:44px;width:190px}
.welcome-title{font-size:16px;font-weight:500;line-height:1.2}
.welcome-copy p{font-size:5.6px;line-height:2.05;color:var(--muted);margin-top:12px}
.welcome-copy .pill{margin-top:11px}
.welcome-photo{position:absolute;border-radius:50%;border:4px solid var(--teal);background:var(--photo-pets)}

/* rooms */
.rooms{background:var(--panel)}
.rooms-row{position:absolute;left:44px;right:44px;display:flex;gap:6px}
.room{flex:1;position:relative;border-radius:2px;overflow:hidden;background:linear-gradient(180deg,var(--photo-room) 0%,var(--photo-room) 55%,#3d3b3e 100%)}
.room-label{position:absolute;bottom:9px;width:100%;text-align:center;color:#fff;font-size:7px;font-weight:500;line-height:1.3}
.arrow{position:absolute;width:9px;height:9px}
.arrow path{fill:none;stroke:var(--ink);stroke-width:1.4}

/* accommodations */
.acc-grid{position:absolute;left:44px;right:44px;display:grid;gap:5px}
.acc-row{display:grid;gap:5px}
.acc-cta{position:absolute;left:50%;transform:translateX(-50%)}
.acc-map{position:absolute;left:50%;transform:translateX(-50%);background:var(--map);border-radius:4px}

/* courses */
.courses{background:var(--panel)}
.course-grid{position:absolute;left:44px;right:44px;display:grid;grid-template-columns:repeat(3,1fr);gap:7px}
.course{background:#fff;border-radius:3px;box-shadow:0 1px 4px rgba(0,0,0,.08);text-align:center;overflow:hidden}
.course-photo{height:95px}
.course-name{font-size:8px;font-weight:500;margin-top:9px}
.course-text{font-size:5.4px;line-height:1.75;color:var(--muted);margin:5px 10px 0}
.course .pill{margin:6px 0 9px;padding:5px 9px}
.courses-more{position:absolute;left:0;right:0;text-align:center;font-size:6px;font-weight:500;color:var(--teal);text-transform:uppercase}

/* reach */
.reach-row{position:absolute;display:grid;grid-template-columns:repeat(4,1fr);text-align:center}
.reach-icon{width:62px;height:62px;margin:0 auto;border-radius:50%;border:2px solid var(--ink);display:flex;align-items:center;justify-content:center}
.reach-icon svg{width:30px;height:30px;fill:var(--teal)}
.reach-name{font-size:7.5px;font-weight:500;margin-top:8px}
.reach-note{font-size:5.5px;color:var(--muted);line-height:1.6;margin-top:3px}

/* testimonials */
.testimonials-media{position:absolute;inset:0;background:#349a90}
.testimonials .section-title{color:#fff;position:relative}
.quote{position:absolute;display:flex;gap:18px;align-items:flex-start}
.avatar{flex:none;width:58px;height:58px;border-radius:50%;background:var(--plum);overflow:hidden;position:relative}
.avatar svg{position:absolute;inset:0;fill:#fff}
.quote p{font-size:6.6px;font-style:italic;line-height:1.8;color:#fff}
.quote-name{font-size:7.5px;font-weight:500;color:#fff;margin-top:8px}

/* contact */
.contact-form{position:absolute;left:44px;width:200px}
.field{height:17px;border:1px solid var(--line);font-size:5.5px;color:var(--muted);padding:5px}
.field + .field{margin-top:7px}
.field--area{height:50px}
.contact-form .pill{margin-top:12px;padding:6px 10px}
.contact-photo{position:absolute;background:var(--photo-husky)}

/* footer */
.footer{background:var(--plum);color:#fff}
.footer-brand{position:absolute;left:44px;display:flex;align-items:center;gap:7px;font-size:19px;font-weight:600}
.footer-brand .brand-dot{background:#fff;width:18px;height:18px}
.footer-col{position:absolute;font-size:5.6px;line-height:2}
.footer-col h4{font-size:6px;font-weight:600;text-transform:uppercase;margin-bottom:6px;line-height:1}
.info-line{display:flex;gap:4px;align-items:flex-start;margin-bottom:10px;line-height:1.9}
.info-line svg{flex:none;width:5px;height:6px;margin-top:2px;fill:var(--teal-soft)}
.footer-bar{position:absolute;left:44px;right:44px;border-top:1px solid rgba(255,255,255,.2);display:flex;justify-content:space-between;align-items:center;padding-top:8px;font-size:5.6px}
.socials{display:flex;gap:3px}
.socials span{width:15px;height:15px;border-radius:50%;border:1px solid rgba(255,255,255,.8)}

/* photo tones */
.tone-lake{background:#6f93bd}
.tone-shore{background:#7f9c9a}
.tone-street{background:#77736b}
.tone-sign{background:#c56d33}
.tone-white{background:#b9cde3}
.tone-dental{background:#4f9a8c}
.tone-sleep{background:#c99a74}
.tone-eye{background:#8e8f9c}
.tone-cart{background:#c6a98a}
.tone-grass{background:#a4a257}
.tone-paw{background:#b9b6a6}
</style>
</head>
<body>
<div class="stage">

<!-- Layout A -->
<div class="page page--a">
  <header class="section site-header" style="height:48px">
    <div class="brand"><span class="brand-dot"></span>Veterra</div>
    <div class="header-right">
      <div class="header-contact"><svg viewBox="0 0 10 10"><path d="M2 0l2 2-1 2 3 3 2-1 2 2-2 2C4 10 0 6 0 2z"/></svg>1 800 555 0147 &nbsp;|&nbsp; <svg viewBox="0 0 10 8"><path d="M0 0h10v8H0z"/></svg>info@veterratraining.example</div>
      <nav class="nav"><span class="is-active">Home</span><span>About us</span><span>Courses</span><span>Accomodation</span><span>Contact us</span></nav>
    </div>
  </header>

  <section class="section hero" style="height:255px">
    <div class="hero-media" role="img" aria-label="Smiling vet in teal scrubs holding a French bulldog"></div>
    <div class="hero-copy">
      <h1 class="hero-title">Outstanding<br>Veterinary<br>Training Center</h1>
      <span class="pill pill--white">Book a workshop</span>
    </div>
    <div class="dots" style="top:226px"><span></span><span></span><span></span></div>
  </section>

  <section class="section welcome" style="height:239px">
    <div class="welcome-copy" style="top:37px">
      <h2 class="welcome-title">Welcome to Veterra<br>Training Center</h2>
      <p>Lorem ipsum dolor sit amet, consectetur adipiscing elise do eiusmod tempor incididunt ut.</p>
      <p>Nioostrud exercitation ullamco laboris nisi ut aliquip ealo mmodo consequat. Duis aute irure dolor in reprehenrit in voluptate velit esse cillum dolore eu fugiat nulla pariatur teur sint occaecat cupidatat sunt.</p>
      <span class="pill pill--teal">Read more</span>
    </div>
    <div class="welcome-photo" style="left:240px;top:20px;width:195px;height:195px" role="img" aria-label="Tricolour dog sitting beside a tabby cat"></div>
  </section>

  <section class="section rooms" style="height:198px">
    <h2 class="section-title" style="padding-top:24px">Our Rooms</h2>
    <svg class="arrow" style="left:22px;top:108px" viewBox="0 0 10 10"><path d="M7 1L3 5l4 4"/></svg>
    <svg class="arrow" style="right:22px;top:108px" viewBox="0 0 10 10"><path d="M3 1l4 4-4 4"/></svg>
    <div class="rooms-row" style="top:56px;height:116px">
      <div class="room" role="img" aria-label="Seminar room with rows of desks"><div class="room-label">Seminar<br>Room</div></div>
      <div class="room" role="img" aria-label="Vet lab training room"><div class="room-label">Vet Lab<br>Training Room</div></div>
      <div class="room" role="img" aria-label="Board and meeting room"><div class="room-label">Board and<br>Meeting Rooms</div></div>
      <div class="room" role="img" aria-label="Kitchen facilities"><div class="room-label">Kitchen<br>Facilities</div></div>
    </div>
  </section>

  <section class="section accommodations" style="height:360px">
    <h2 class="section-title" style="padding-top:23px">Our Accommodations</h2>
    <div class="acc-grid" style="top:55px">
      <div class="acc-row" style="grid-template-columns:1fr 1fr;height:120px">
        <div class="tone-lake" role="img" aria-label="Lakeside hotel facade"></div>
        <div class="tone-shore" role="img" aria-label="Curved hotel building by a lake"></div>
      </div>
      <div class="acc-row" style="grid-template-columns:1fr 1fr 1fr;height:109px">
        <div class="tone-street" role="img" aria-label="Hotel entrance on a city street"></div>
        <div class="tone-sign" role="img" aria-label="Illuminated hotel sign"></div>
        <div class="tone-white" role="img" aria-label="Modern white hotel building"></div>
      </div>
    </div>
    <span class="pill pill--teal acc-cta" style="top:307px">View more</span>
  </section>

  <section class="section courses" style="height:487px">
    <h2 class="section-title" style="padding-top:22px">Courses</h2>
    <div class="course-grid" style="top:51px">
      <div class="course"><div class="course-photo tone-dental" role="img" aria-label="Vet checking a puppy's teeth"></div><div class="course-name">Dentistry for vets</div><p class="course-text">Nemo enim ipsam voluptatem quia voluptas sit aspernatur aud it aut fugi sed quia conse.</p><span class="pill pill--teal">Book now</span></div>
      <div class="course"><div class="course-photo tone-sleep" role="img" aria-label="Sedated dog under anaesthesia"></div><div class="course-name">Anaesthesia</div><p class="course-text">Nemo enim ipsam voluptatem quia voluptas sit aspernatur aud it aut fugi sed quia conse.</p><span class="pill pill--teal">Book now</span></div>
      <div class="course"><div class="course-photo tone-eye" role="img" aria-label="Cat during an eye examination"></div><div class="course-name">Ophthalmology</div><p class="course-text">Nemo enim ipsam voluptatem quia voluptas sit aspernatur aud it aut fugi sed quia conse.</p><span class="pill pill--teal">Book now</span></div>
      <div class="course"><div class="course-photo tone-cart" role="img" aria-label="Dog with a mobility cart"></div><div class="course-name">Orthopaedic</div><p class="course-text">Nemo enim ipsam voluptatem quia voluptas sit aspernatur aud it aut fugi sed quia conse.</p><span class="pill pill--teal">Book now</span></div>
      <div class="course"><div class="course-photo tone-grass" role="img" aria-label="Dog and cat playing on grass"></div><div class="course-name">Behaviour</div><p class="course-text">Nemo enim ipsam voluptatem quia voluptas sit aspernatur aud it aut fugi sed quia conse.</p><span class="pill pill--teal">Book now</span></div>
      <div class="course"><div class="course-photo tone-paw" role="img" aria-label="Vet bandaging a dog's paw"></div><div class="course-name">Emergency Care</div><p class="course-text">Nemo enim ipsam voluptatem quia voluptas sit aspernatur aud it aut fugi sed quia conse.</p><span class="pill pill--teal">Book now</span></div>
    </div>
    <div class="courses-more" style="top:454px">View more</div>
  </section>

  <section class="section reach" style="height:193px">
    <h2 class="section-title" style="padding-top:30px">How To Reach Us</h2>
    <div class="reach-row" style="top:57px;left:27px;right:27px">
      <div><div class="reach-icon"><svg viewBox="0 0 24 24"><path d="M5 11l2-5h10l2 5h1v6h-2v2h-3v-2H9v2H6v-2H4v-6zM8 8l-1 3h10l-1-3zM7 13a1 1 0 100 2 1 1 0 000-2zm10 0a1 1 0 100 2 1 1 0 000-2z"/></svg></div><div class="reach-name">Car</div><div class="reach-note">Nearest Landmark<br>Clock Tower</div></div>
      <div><div class="reach-icon"><svg viewBox="0 0 24 24"><path d="M7 3h10a2 2 0 012 2v10a2 2 0 01-2 2l2 4h-2l-2-4H9l-2 4H5l2-4a2 2 0 01-2-2V5a2 2 0 012-2zm0 3v4h4V6zm6 0v4h4V6zM8 13a1 1 0 100 2 1 1 0 000-2zm8 0a1 1 0 100 2 1 1 0 000-2z"/></svg></div><div class="reach-name">Train</div><div class="reach-note">Nearest Railway Station<br>Eiusmod tempor</div></div>
      <div><div class="reach-icon"><svg viewBox="0 0 24 24"><path d="M21 12c0-1-1-1.5-2-1.5h-5L9 3H7l3 7.5H5L3 8H2l1 4-1 4h1l2-2.5h5L7 21h2l5-7.5h5c1 0 2-.5 2-1.5z"/></svg></div><div class="reach-name">Flight</div><div class="reach-note">Nearest Airport<br>Eiusmod tempor</div></div>
      <div><div class="reach-icon"><svg viewBox="0 0 24 24"><path d="M6 3h12a2 2 0 012 2v13h-1v2h-3v-2H8v2H5v-2H4V5a2 2 0 012-2zm0 3v6h12V6zm1 8a1 1 0 100 2 1 1 0 000-2zm10 0a1 1 0 100 2 1 1 0 000-2z"/></svg></div><div class="reach-name">Bus</div><div class="reach-note">Nearest Bus stop<br>Eiusmod tempor</div></div>
    </div>
  </section>

  <section class="section testimonials" style="height:175px">
    <div class="testimonials-media" role="img" aria-label="Teal-tinted photo of a vet with a pet"></div>
    <h2 class="section-title" style="padding-top:20px">Testimonials</h2>
    <div class="quote" style="left:62px;right:44px;top:62px">
      <div class="avatar"><svg viewBox="0 0 58 58"><circle cx="29" cy="22" r="10"/><path d="M10 52c2-12 10-17 19-17s17 5 19 17z"/></svg></div>
      <div><p>“ At vero eos et accusamus et iusto odio dignissimosers ducimus qui blanditiis ntium voluptatum deleniti atque corrupti quos dolores et quas molestias excep turi sint occae coti cupiditate non provident, similique sunt in culpa qui officiad mollitia animi, id est laborum et dolorum facilis est ”</p><div class="quote-name">Jane Roe</div></div>
    </div>
    <div class="dots" style="top:140px"><span></span><span></span><span></span></div>
  </section>

  <section class="section contact" style="height:250px">
    <h2 class="section-title" style="padding-top:28px">Contact Us</h2>
    <form class="contact-form" style="top:62px">
      <div class="field">Name*</div><div class="field">Email*</div><div class="field">Subject*</div><div class="field field--area">Message</div>
      <span class="pill pill--teal">Submit</span>
    </form>
    <div class="contact-photo" style="left:262px;top:62px;width:163px;height:153px" role="img" aria-label="Vet examining a husky"></div>
  </section>

  <footer class="section footer" style="height:173px">
    <div class="footer-brand" style="top:60px"><span class="brand-dot"></span>Veterra</div>
    <div class="footer-col" style="left:203px;top:24px"><h4>Quick links</h4>Home<br>About us<br>Courses<br>Accomodation<br>Contact us<br>Privacy statement<br>Terms &amp; conditions</div>
    <div class="footer-col" style="left:300px;top:24px;width:140px"><h4>Contact information</h4>
      <div class="info-line"><svg viewBox="0 0 10 12"><path d="M5 0a4 4 0 014 4c0 3-4 8-4 8S1 7 1 4a4 4 0 014-4z"/></svg><span>Lindenweg 12 - 14<br>D-80000 Musterstadt</span></div>
      <div class="info-line"><svg viewBox="0 0 10 10"><path d="M2 0l2 2-1 2 3 3 2-1 2 2-2 2C4 10 0 6 0 2z"/></svg><span>1 800 555 0147</span></div>
      <div class="info-line"><svg viewBox="0 0 10 8"><path d="M0 0h10v8H0z"/></svg><span>info@veterratraining.example</span></div>
    </div>
    <div class="footer-bar" style="top:142px"><span>© 2021 Veterra Training Center. All Rights Reserved.</span><div class="socials"><span></span><span></span><span></span></div></div>
  </footer>
</div>

<!-- Layout B -->
<div class="page page--b">
  <header class="section site-header" style="height:49px">
    <div class="brand"><span class="brand-dot"></span>Veterra</div>
    <div class="header-right">
      <div class="header-contact"><svg viewBox="0 0 10 10"><path d="M2 0l2 2-1 2 3 3 2-1 2 2-2 2C4 10 0 6 0 2z"/></svg>1 800 555 0147 &nbsp;|&nbsp; <svg viewBox="0 0 10 8"><path d="M0 0h10v8H0z"/></svg>info@veterratraining.example</div>
      <nav class="nav"><span class="is-active">Home</span><span>About us</span><span>Courses</span><span>Accomodation</span><span>Contact us</span></nav>
    </div>
  </header>

  <section class="section hero" style="height:260px">
    <div class="hero-media" role="img" aria-label="Smiling vet in teal scrubs holding a French bulldog"></div>
    <div class="hero-copy" style="top:62px">
      <h1 class="hero-title" style="font-size:21px">Outstanding<br>Veterinary<br>Training Center</h1>
      <span class="pill pill--white">Book a workshop</span>
    </div>
    <div class="dots" style="top:232px"><span></span><span></span><span></span></div>
  </section>

  <section class="section welcome" style="height:244px">
    <div class="welcome-copy" style="top:38px;width:195px">
      <h2 class="welcome-title">Welcome to Veterra<br>Training Center</h2>
      <p>Lorem ipsum dolor sit amet, consectetur adipiscing elise do eiusmod tempor incididunt ut.</p>
      <p>Nioostrud exercitation ullamco laboris nisi ut aliquip ealo mmodo consequat. Duis aute irure dolor in reprehenrit in voluptate velit esse cillum dolore eu fugiat nulla pariatur teur sint occaecat cupidatat sunt.</p>
      <span class="pill pill--teal">Read more</span>
    </div>
    <div class="welcome-photo" style="left:245px;top:20px;width:200px;height:200px" role="img" aria-label="Tricolour dog sitting beside a tabby cat"></div>
  </section>

  <section class="section rooms" style="height:202px">
    <h2 class="section-title" style="padding-top:26px">Our Rooms</h2>
    <svg class="arrow" style="left:23px;top:111px" viewBox="0 0 10 10"><path d="M7 1L3 5l4 4"/></svg>
    <svg class="arrow" style="right:23px;top:111px" viewBox="0 0 10 10"><path d="M3 1l4 4-4 4"/></svg>
    <div class="rooms-row" style="top:58px;height:118px">
      <div class="room" role="img" aria-label="Seminar room with rows of desks"><div class="room-label">Seminar<br>Room</div></div>
      <div class="room" role="img" aria-label="Vet lab training room"><div class="room-label">Vet Lab<br>Training Room</div></div>
      <div class="room" role="img" aria-label="Board and meeting room"><div class="room-label">Board and<br>Meeting Rooms</div></div>
      <div class="room" role="img" aria-label="Kitchen facilities"><div class="room-label">Kitchen<br>Facilities</div></div>
    </div>
  </section>

  <section class="section accommodations" style="height:322px">
    <h2 class="section-title" style="padding-top:24px">Our Accommodations</h2>
    <div class="acc-map" style="top:52px;width:182px;height:248px" role="img" aria-label="Map of Germany with pins marking recommended hotels"></div>
  </section>

  <section class="section courses" style="height:495px">
    <h2 class="section-title" style="padding-top:20px">Courses</h2>
    <div class="course-grid" style="top:50px;gap:7px 8px">
      <div class="course"><div class="course-photo tone-dental" style="height:97px" role="img" aria-label="Vet checking a puppy's teeth"></div><div class="course-name">Dentistry for vets</div><p class="course-text">Nemo enim ipsam voluptatem quia voluptas sit aspernatur aud it aut fugi sed quia conse.</p><span class="pill pill--teal">Book now</span></div>
      <div class="course"><div class="course-photo tone-sleep" style="height:97px" role="img" aria-label="Sedated dog under anaesthesia"></div><div class="course-name">Anaesthesia</div><p class="course-text">Nemo enim ipsam voluptatem quia voluptas sit aspernatur aud it aut fugi sed quia conse.</p><span class="pill pill--teal">Book now</span></div>
      <div class="course"><div class="course-photo tone-eye" style="height:97px" role="img" aria-label="Cat during an eye examination"></div><div class="course-name">Ophthalmology</div><p class="course-text">Nemo enim ipsam voluptatem quia voluptas sit aspernatur aud it aut fugi sed quia conse.</p><span class="pill pill--teal">Book now</span></div>
      <div class="course"><div class="course-photo tone-cart" style="height:97px" role="img" aria-label="Dog with a mobility cart"></div><div class="course-name">Orthopaedic</div><p class="course-text">Nemo enim ipsam voluptatem quia voluptas sit aspernatur aud it aut fugi sed quia conse.</p><span class="pill pill--teal">Book now</span></div>
      <div class="course"><div class="course-photo tone-grass" style="height:97px" role="img" aria-label="Dog and cat playing on grass"></div><div class="course-name">Behaviour</div><p class="course-text">Nemo enim ipsam voluptatem quia voluptas sit aspernatur aud it aut fugi sed quia conse.</p><span class="pill pill--teal">Book now</span></div>
      <div class="course"><div class="course-photo tone-paw" style="height:97px" role="img" aria-label="Vet bandaging a dog's paw"></div><div class="course-name">Emergency Care</div><p class="course-text">Nemo enim ipsam voluptatem quia voluptas sit aspernatur aud it aut fugi sed quia conse.</p><span class="pill pill--teal">Book now</span></div>
    </div>
    <div class="courses-more" style="top:464px">View more</div>
  </section>

  <section class="section reach" style="height:199px">
    <h2 class="section-title" style="padding-top:30px">How To Reach Us</h2>
    <div class="reach-row" style="top:58px;left:39px;right:39px">
      <div><div class="reach-icon" style="width:64px;height:64px"><svg viewBox="0 0 24 24"><path d="M5 11l2-5h10l2 5h1v6h-2v2h-3v-2H9v2H6v-2H4v-6zM8 8l-1 3h10l-1-3zM7 13a1 1 0 100 2 1 1 0 000-2zm10 0a1 1 0 100 2 1 1 0 000-2z"/></svg></div><div class="reach-name">Car</div><div class="reach-note">Nearest Landmark<br>Clock Tower</div></div>
      <div><div class="reach-icon" style="width:64px;height:64px"><svg viewBox="0 0 24 24"><path d="M7 3h10a2 2 0 012 2v10a2 2 0 01-2 2l2 4h-2l-2-4H9l-2 4H5l2-4a2 2 0 01-2-2V5a2 2 0 012-2zm0 3v4h4V6zm6 0v4h4V6zM8 13a1 1 0 100 2 1 1 0 000-2zm8 0a1 1 0 100 2 1 1 0 000-2z"/></svg></div><div class="reach-name">Train</div><div class="reach-note">Nearest Railway Station<br>Eiusmod tempor</div></div>
      <div><div class="reach-icon" style="width:64px;height:64px"><svg viewBox="0 0 24 24"><path d="M21 12c0-1-1-1.5-2-1.5h-5L9 3H7l3 7.5H5L3 8H2l1 4-1 4h1l2-2.5h5L7 21h2l5-7.5h5c1 0 2-.5 2-1.5z"/></svg></div><div class="reach-name">Flight</div><div class="reach-note">Nearest Airport<br>Eiusmod tempor</div></div>
      <div><div class="reach-icon" style="width:64px;height:64px"><svg viewBox="0 0 24 24"><path d="M6 3h12a2 2 0 012 2v13h-1v2h-3v-2H8v2H5v-2H4V5a2 2 0 012-2zm0 3v6h12V6zm1 8a1 1 0 100 2 1 1 0 000-2zm10 0a1 1 0 100 2 1 1 0 000-2z"/></svg></div><div class="reach-name">Bus</div><div class="reach-note">Nearest Bus stop<br>Eiusmod tempor</div></div>
    </div>
  </section>

  <section class="section testimonials" style="height:178px">
    <div class="testimonials-media" role="img" aria-label="Teal-tinted photo of a vet with a pet"></div>
    <h2 class="section-title" style="padding-top:20px">Testimonials</h2>
    <div class="quote" style="left:64px;right:44px;top:63px">
      <div class="avatar" style="width:60px;height:60px"><svg viewBox="0 0 58 58"><circle cx="29" cy="22" r="10"/><path d="M10 52c2-12 10-17 19-17s17 5 19 17z"/></svg></div>
      <div><p>“ At vero eos et accusamus et iusto odio dignissimosers ducimus qui blanditiis ntium voluptatum deleniti atque corrupti quos dolores et quas molestias excep turi sint occae coti cupiditate non provident, similique sunt in culpa qui officiad mollitia animi, id est laborum et dolorum facilis est ”</p><div class="quote-name">Jane Roe</div></div>
    </div>
    <div class="dots" style="top:142px"><span></span><span></span><span></span></div>
  </section>

  <section class="section contact" style="height:256px">
    <h2 class="section-title" style="padding-top:28px">Contact Us</h2>
    <form class="contact-form" style="top:63px;width:205px">
      <div class="field">Name*</div><div class="field">Email*</div><div class="field">Subject*</div><div class="field field--area">Message</div>
      <span class="pill pill--teal">Submit</span>
    </form>
    <div class="contact-photo" style="left:268px;top:63px;width:166px;height:157px" role="img" aria-label="Vet examining a husky"></div>
  </section>

  <footer class="section footer" style="height:173px">
    <div class="footer-brand" style="top:60px"><span class="brand-dot"></span>Veterra</div>
    <div class="footer-col" style="left:207px;top:24px"><h4>Quick links</h4>Home<br>About us<br>Courses<br>Accomodation<br>Contact us<br>Privacy statement<br>Terms &amp; conditions</div>
    <div class="footer-col" style="left:306px;top:24px;width:140px"><h4>Contact information</h4>
      <div class="info-line"><svg viewBox="0 0 10 12"><path d="M5 0a4 4 0 014 4c0 3-4 8-4 8S1 7 1 4a4 4 0 014-4z"/></svg><span>Lindenweg 12 - 14<br>D-80000 Musterstadt</span></div>
      <div class="info-line"><svg viewBox="0 0 10 10"><path d="M2 0l2 2-1 2 3 3 2-1 2 2-2 2C4 10 0 6 0 2z"/></svg><span>1 800 555 0147</span></div>
      <div class="info-line"><svg viewBox="0 0 10 8"><path d="M0 0h10v8H0z"/></svg><span>info@veterratraining.example</span></div>
    </div>
    <div class="footer-bar" style="top:142px"><span>© 2021 Veterra Training Center. All Rights Reserved.</span><div class="socials"><span></span><span></span><span></span></div></div>
  </footer>
</div>

</div>
</body>
</html>
```